Logo and Website Design for QR.KA Horizon - a Software Engineering and IT company

Software engineering and IT are two different disciplines - and yet inseparably linked. At QR.KA Horizon, we combine both worlds and ensure that our software solutions are not only innovative and powerful, but also integrate perfectly into existing IT landscapes. Vision stands more for imagination, so it is not neccessary something what has to do with visualisation. Please consider that the winning competitor is also instructed to make a logo for the company. So please make a suitable logo for QR.KA Horizon to which the website fits to and show it during the website creation process. A good Logo desing is important for winning the competition. The website should contain a landing page with inspiring, perhaps futuristic photos of a datacenter and lines of code. Eventuelly flewent integrated in the text. On the landing page the company should introduced with a small text (max 250 words) followed by a section with a short text to one of our products nearby a graphic visualising the architecture of the product. The menue should be on top and fixed during scrolling and consist of the menue items home, solutions, who are we and a contact button. There should be a footer for linking social media, rights and Impressum. Only as an idea not a must. The very first view on the landing page could also be the menue bar and below of it a transparent unsharp photo (e.g. datacenter, lines of code, both ;) with the company name in the center.

###############################################################

Hi Designers,

Despite your very good approaches for describing QR.KA Horizon, here a short introduction (german text) from ourself:

------
QR.KA Horizon – Ihr Partner für ganzheitliche Softwarelösungen

Die QR.KA Horizon ist ein dynamisches Unternehmen, das sich nicht nur auf die Konzeption, das Design und die Entwicklung maßgeschneiderter Software spezialisiert hat, sondern auch deren reibungslosen Betrieb sicherstellt. Mit einem Team aus erfahrenen Softwarearchitekten und IT-Professionals verbinden wir modernste Softwareentwicklung mit tiefgehendem IT-Know-how – für Lösungen, die nachhaltig, leistungsstark und zukunftssicher sind.

Software Engineering trifft IT – Perfektion in Kombination
Software Engineering und IT sind zwei unterschiedliche Disziplinen – und doch untrennbar miteinander verbunden. Wir bei QR.KA Horizon vereinen beide Welten und sorgen dafür, dass unsere Softwarelösungen nicht nur innovativ und leistungsfähig sind, sondern sich auch perfekt in bestehende IT-Landschaften integrieren.

Expertise mit Fokus auf Healthcare & komplexe IT-Umgebungen
Unsere Experten bringen jahrzehntelange Erfahrung aus dem Healthcare-Sektor mit und unterstützen IT-Abteilungen großer Kliniken in der Entwicklung und Optimierung von Softwarelösungen. Von Anwendungssoftware bis hin zu Steuerungssystemen – unsere Softwareingenieure wissen genau, worauf es ankommt.

Ganzheitlicher Ansatz – über die Software hinaus
Wir entwickeln nicht nur Software, sondern übernehmen auch die Verantwortung für deren stabile und effiziente Betriebsumgebung. Egal, ob on-premises, in der Cloud oder als SaaS-Lösung – wir kümmern uns um den kompletten Lifecycle Ihrer Anwendung.

Ihre Vision – unsere Mission.
Ob Neuentwicklung einer SaaS-Anwendung oder die Migration bestehender Lösungen in eine moderne SaaS-Umgebung – mit QR.KA Horizon haben Sie einen starken Partner an Ihrer Seite.

Lassen Sie uns gemeinsam die Zukunft Ihrer Software gestalten!
--------------

Our first solution called "Clear Record Transfer Gateway" (CLURA)
-------------------
Teilen Sie Ihre Daten sicher – ohne Kompromisse!

Sie nutzen eine relationale Datenbank (Brightcask, Tabulon Hub, Vellumdb etc.) und möchten ausgewählte Daten mit Dritten teilen – sei es für ein Data Warehouse, Business Controller, Lieferanten oder Kunden? Doch dabei sollen Datensicherheit, Integrität und Verfügbarkeit Ihrer primären Lösung in keiner Weise gefährdet werden?

Mit unserer Lösung erhalten Sie genau das: Maximalen Schutz für Ihre Anwendung bei gleichzeitigem Nutzen durch autorisierte Dritte – ganz ohne teure Lizenzkosten für eine Schattendatenbank.

Lassen Sie uns gemeinsam herausfinden, wie Sie Ihre Daten sicher und effizient nutzen können. Kontaktieren Sie uns – wir zeigen Ihnen, was möglich ist!
---------------------

Our second solution MIVO:
---------------------
MIVO – Program for a Tone Matching Instrument ist die smarte Lösung für Unternehmen, die bei Farbgenauigkeit keine Kompromisse machen. Die Software erkennt Farbabweichungen zwischen Mustern vollautomatisch, beschreibt sie verständlich und sorgt so für gleichbleibend hohe Produktqualität – schnell, visuell und präzise. Perfekt für alle, die Farbe zur Vertrauenssache machen.
-------------------------

Thanks,
Gerold

Target Market(s)

IT Professionals from any sector

Industry/Entity Type

Healthcare and other

Coding

Coded - Design and coding required

Number of Pages Required

1 page

Font styles to use
Sans Serif

Colors
0054AA
0677BA
7BADD7
CADEEF
E8F1F8
0094D4
00A9DD
6FCCEA
C7EBF8
E9F6FB
00AB8E
00BBA5
67D7C9
C6EFE9
E9F9F6

Requirements
Must have
• Please see description
Nice to have
• On the landing page the company should introduced with a small text (max 250 words) followed by a section with a short text to one of our products nearby a graphic visualising the architecture of the product. The menue should be on top and fixed during scrolling and consist of the menue items home, solutions, who are we and a contact button. There should be a footer for linking social media, rights and Impressum. Only as an idea not a must. The very first view on the landing page could also be the menue bar and below of it a transparent unsharp photo (e.g. datacenter, lines of code, both ;) with the company name in the center.
Should not have
• Please see description

```html
<!DOCTYPE html>
<html lang="en">
<head>
<meta charset="utf-8">
<title>QR.KA Horizon – Software Engineering &amp; IT</title>
<link href="https://fonts.googleapis.com/css2?family=Montserrat:wght@400;500;600;700;800&family=Poppins:wght@700;800&display=swap" rel="stylesheet">
<style>
:root{
  --blue-deep:#0054AA;
  --blue:#0677BA;
  --blue-mid:#1f6fa8;
  --blue-soft:#CADEEF;
  --blue-pale:#E8F1F8;
  --sky:#0094D4;
  --cyan:#00A9DD;
  --teal:#00AB8E;
  --teal-bright:#00BBA5;
  --ink:#111418;
  --text:#222222;
  --footer:#262626;
  --white:#ffffff;
}
*{box-sizing:border-box;margin:0;padding:0}
html,body{width:1200px;height:3402px;overflow:hidden}
body{position:relative;font-family:"Montserrat",sans-serif;color:var(--text);background:var(--white)}
.abs{position:absolute}
.btn-grad{display:flex;align-items:center;justify-content:center;color:var(--white);font-weight:600;font-size:16px;letter-spacing:.3px;border-radius:6px 18px 6px 18px;background:linear-gradient(90deg,var(--teal) 0%,var(--blue-mid) 100%);text-decoration:none}
.btn-ghost{display:flex;align-items:center;justify-content:center;color:var(--white);font-weight:600;font-size:16px;border:2px solid var(--white);border-radius:6px 20px 6px 20px;text-decoration:none}

/* header */
.site-header{left:0;top:0;width:1200px;height:86px;background:var(--white);z-index:5;box-shadow:0 1px 4px rgba(0,0,0,.06)}
.brand{left:113px;top:10px;display:flex;align-items:center;gap:12px}
.brand-dot{width:62px;height:62px;border-radius:50%;background:var(--teal)}
.brand-name{font-weight:700;font-size:23px;line-height:26px;color:var(--blue-mid)}
.nav a{position:absolute;top:41px;font-size:15px;color:#222;text-decoration:none;font-weight:500}
.nav a.active{color:var(--blue-mid);font-weight:700}
.header-cta{left:908px;top:22px;width:176px;height:46px}

/* hero */
.hero{left:0;top:86px;width:1200px;height:630px;
  background:
    radial-gradient(ellipse 22% 30% at 50% 62%,rgba(150,215,255,.75) 0%,rgba(60,150,230,.35) 45%,transparent 100%),
    radial-gradient(ellipse 60% 80% at 50% 55%,#2a7fd0 0%,#155aa6 35%,transparent 75%),
    linear-gradient(90deg,#061a38 0%,#0c3a74 18%,#0f4d92 35%,#12559c 50%,#0f4d92 65%,#0c3a74 82%,#061a38 100%)}
.hero-copy{left:0;top:186px;width:1200px;text-align:center;color:var(--white);text-shadow:0 2px 10px rgba(0,20,60,.5)}
.hero-welcome{font-weight:700;font-size:26px;letter-spacing:.5px}
.hero-title{font-weight:800;font-size:70px;line-height:1;margin-top:16px;letter-spacing:1px}
.hero-lead{font-size:15.5px;line-height:30px;margin-top:14px}
.hero-btn{left:509px;top:388px;width:178px;height:47px}

/* section headings */
.sec-title{font-weight:800;font-size:40px;color:var(--ink);text-align:center;width:1200px;left:0}
.sec-title .accent{color:var(--teal)}
.rule{height:5px;border-radius:3px;background:var(--blue-mid)}

/* about */
.about-photo{left:118px;top:815px;width:444px;height:440px;border-radius:50%;
  background:
    radial-gradient(circle at 70% 30%,#f1f3f6 0%,rgba(241,243,246,0) 45%),
    radial-gradient(circle at 30% 45%,#c9b8a6 0%,rgba(201,184,166,0) 30%),
    radial-gradient(circle at 55% 85%,#eef0f2 0%,rgba(238,240,242,0) 40%),
    linear-gradient(135deg,#dfe3e8 0%,#c6ccd4 55%,#a9b2bd 100%)}
.about-title{left:636px;top:806px;font-weight:800;font-size:39px;color:var(--ink)}
.about-text{left:643px;top:908px;width:420px;font-size:13.6px;line-height:28.3px;color:var(--text)}
.about-btn{left:645px;top:1195px;width:176px;height:46px}

/* solutions */
.solutions-band{left:0;top:1330px;width:1200px;height:700px}
.card{width:298px;height:279px;background:var(--white);border-radius:6px;box-shadow:0 4px 14px rgba(0,40,80,.18);overflow:hidden}
.card-media{margin:3px;height:188px;border-radius:3px}
.card-label{position:absolute;left:16px;top:204px;font-weight:600;font-size:17px;line-height:29px;color:#1a1a1a}
.card-icon{position:absolute;right:16px;top:206px}
.arrow{width:44px;height:44px;border-radius:50%;display:flex;align-items:center;justify-content:center}

/* products */
.product{left:175px;top:2186px;width:835px;height:425px;border-radius:4px;
  background:
    radial-gradient(ellipse 40% 45% at 75% 40%,rgba(90,180,240,.55) 0%,rgba(40,120,190,.2) 55%,transparent 100%),
    radial-gradient(ellipse 45% 30% at 70% 90%,rgba(30,190,160,.45) 0%,transparent 100%),
    linear-gradient(110deg,#1c5476 0%,#174a6e 30%,#0f3c62 55%,#0b3556 75%,#0c4a5c 100%)}
.product-title{left:215px;top:2286px;font-family:"Poppins",sans-serif;font-weight:800;font-size:42px;line-height:50px;color:var(--white)}
.product-text{left:219px;top:2404px;width:310px;font-size:13.6px;line-height:28.5px;color:var(--white)}
.product-btn{left:221px;top:2509px;width:179px;height:51px}

/* cta */
.cta{left:0;top:2700px;width:1200px;height:380px;
  background:
    radial-gradient(ellipse 30% 50% at 85% 40%,rgba(255,255,255,.6) 0%,transparent 100%),
    radial-gradient(ellipse 35% 50% at 15% 70%,rgba(180,205,228,.7) 0%,transparent 100%),
    linear-gradient(180deg,#e6edf4 0%,#d3e1ed 100%)}
.cta-title{left:112px;top:2772px;font-weight:800;font-size:40px;line-height:48px;color:var(--ink)}
.cta-title .accent{color:var(--teal)}
.cta-btn{left:909px;top:2795px;width:176px;height:47px}

/* footer */
.footer-body{left:0;top:3040px;width:1200px;height:362px;background:var(--footer)}
.footer-brand{left:140px;top:3072px;width:150px;text-align:center;color:var(--white)}
.footer-brand .dot{width:126px;height:126px;border-radius:50%;background:var(--white);margin:0 auto 22px}
.footer-brand .name{font-weight:700;font-size:28px;line-height:34px}
.f-col h4{font-weight:600;font-size:20px;color:var(--white);margin-bottom:22px}
.f-col a{display:block;font-size:15.5px;color:var(--white);text-decoration:none;line-height:32px}
.newsletter p{font-size:13px;line-height:26px;color:var(--white)}
.news-input{left:855px;top:3193px;width:216px;height:43px;border-radius:22px;background:var(--white);display:flex;align-items:center;justify-content:space-between;padding:0 14px 0 12px;font-size:13px;color:#666}
.footer-rule{left:106px;top:3323px;width:977px;height:1px;background:#8a8a8a}
.copyright{left:0;top:3349px;width:1200px;text-align:center;font-size:13.5px;color:var(--white)}
</style>
</head>
<body>

<header class="abs site-header">
  <div class="abs brand"><span class="brand-dot"></span><span class="brand-name">QR.KA<br>Horizon</span></div>
  <nav class="nav">
    <a class="active" href="#" style="left:448px">HOME</a>
    <a href="#" style="left:530px">ABOUT US</a>
    <a href="#" style="left:642px">PRODUCTS</a>
    <a href="#" style="left:760px">SOLUTIONS</a>
  </nav>
  <a class="abs btn-grad header-cta" href="#">CONTACT US</a>
</header>

<section class="abs hero" role="img" aria-label="Data center corridor with glowing blue server racks"></section>
<svg class="abs" style="left:0;top:520px" width="1200" height="200" viewBox="0 0 1200 200">
  <defs><linearGradient id="waveA" x1="0" x2="1"><stop offset="0" stop-color="#0677BA"/><stop offset="1" stop-color="#00AB8E"/></linearGradient></defs>
  <path d="M0,70 Q600,250 1200,70 L1200,200 L0,200Z" fill="#fff"/>
  <path d="M0,70 Q600,250 1200,70" fill="none" stroke="url(#waveA)" stroke-width="14"/>
</svg>
<div class="abs hero-copy">
  <div class="hero-welcome">WELCOME TO</div>
  <div class="hero-title">QR.KA HORIZON</div>
  <p class="hero-lead">Innovative software solutions designed to seamlessly integrate into modern IT<br>landscapes—scalable, efficient, and future-ready</p>
</div>
<a class="abs btn-ghost hero-btn" href="#">GET STARTED</a>

<!-- about -->
<div class="abs about-photo" role="img" aria-label="Two colleagues working together at a laptop in a bright office"></div>
<svg class="abs" style="left:98px;top:808px" width="470" height="456" viewBox="0 0 470 456">
  <defs><linearGradient id="ringGrad" x1="0" y1="0" x2="0.6" y2="1"><stop offset="0" stop-color="#1f6fa8"/><stop offset=".55" stop-color="#1a86a6"/><stop offset="1" stop-color="#00AB8E"/></linearGradient></defs>
  <path d="M190,8 A222,222 0 0 0 250,450" fill="none" stroke="url(#ringGrad)" stroke-width="18" stroke-linecap="round"/>
</svg>
<h2 class="abs about-title"><span style="color:var(--teal)">ABOUT</span> US</h2>
<div class="abs rule" style="left:643px;top:872px;width:87px"></div>
<p class="abs about-text">Lorem Ipsum is simply dummy text of the printing and typesetting industry. Lorem Ipsum has been the industry's standard dummy text ever since the 1500s, when an unknown printer took a galley of type and scrambled it to make a type specimen book. It has survived not only five centuries, but also the leap into electronic typesetting, remaining essentially unchanged.<br>It was popularised in the 1960s with the release of Letraset sheets containing Lorem Ipsum passages,</p>
<a class="abs btn-grad about-btn" href="#">READ MORE</a>

<!-- solutions -->
<svg class="abs solutions-band" viewBox="0 0 1200 700" width="1200" height="700">
  <defs>
    <linearGradient id="bandFill" x1="0" y1="0" x2="1" y2="1"><stop offset="0" stop-color="#e6f0f7"/><stop offset=".5" stop-color="#cfe2ef"/><stop offset="1" stop-color="#dbe9f3"/></linearGradient>
    <radialGradient id="bandGlow" cx=".5" cy=".55" r=".5"><stop offset="0" stop-color="#ffffff" stop-opacity=".55"/><stop offset="1" stop-color="#ffffff" stop-opacity="0"/></radialGradient>
    <linearGradient id="waveB" x1="0" x2="1"><stop offset="0" stop-color="#0677BA"/><stop offset="1" stop-color="#00AB8E"/></linearGradient>
  </defs>
  <path d="M0,140 Q600,-110 1200,110 L1200,570 Q600,755 0,597Z" fill="url(#bandFill)"/>
  <path d="M0,140 Q600,-110 1200,110 L1200,570 Q600,755 0,597Z" fill="url(#bandGlow)"/>
  <path d="M0,140 Q600,-110 1200,110" fill="none" stroke="url(#waveB)" stroke-width="12"/>
  <path d="M0,597 Q600,755 1200,570" fill="none" stroke="url(#waveB)" stroke-width="12"/>
</svg>
<h2 class="abs sec-title" style="top:1440px">OUR <span class="accent">SOLUTIONS</span></h2>
<div class="abs rule" style="left:553px;top:1510px;width:86px"></div>

<div class="abs arrow" style="left:28px;top:1659px;border:2px solid #9aa4ad">
  <svg width="16" height="16" viewBox="0 0 16 16"><path d="M10 2 L4 8 L10 14" fill="none" stroke="#9aa4ad" stroke-width="2"/></svg>
</div>
<div class="abs arrow" style="left:1118px;top:1659px;border:3px solid var(--blue-mid)">
  <svg width="16" height="16" viewBox="0 0 16 16"><path d="M6 2 L12 8 L6 14" fill="none" stroke="#1f6fa8" stroke-width="2.4"/></svg>
</div>

<article class="abs card" style="left:110px;top:1556px">
  <div class="card-media" role="img" aria-label="Magnifying glass over glowing lines of code" style="background:radial-gradient(circle at 62% 45%,#3a6e9c 0%,rgba(58,110,156,0) 35%),radial-gradient(circle at 20% 30%,rgba(220,70,70,.45) 0%,transparent 35%),linear-gradient(135deg,#0b2a4a,#123c66 55%,#1b2230)"></div>
  <div class="card-label">Custom Software<br>Development</div>
  <svg class="card-icon" width="60" height="58" viewBox="0 0 60 58" fill="none" stroke="#0677BA" stroke-width="2.4">
    <rect x="3" y="3" width="46" height="40" rx="5"/><line x1="3" y1="14" x2="49" y2="14"/>
    <path d="M14 24 L9 29 L14 34 M25 24 L30 29 L25 34 M21 22 L18 36"/>
    <circle cx="45" cy="43" r="8" stroke="#00AB8E"/><circle cx="45" cy="43" r="3" stroke="#00AB8E"/>
  </svg>
</article>
<article class="abs card" style="left:451px;top:1556px">
  <div class="card-media" role="img" aria-label="Glowing cloud above a circuit board" style="background:radial-gradient(ellipse 28% 35% at 55% 42%,#f0a35a 0%,rgba(200,110,40,.4) 50%,transparent 100%),radial-gradient(ellipse 50% 30% at 50% 80%,rgba(60,190,220,.5) 0%,transparent 100%),linear-gradient(135deg,#0e2b44,#16506e 60%,#0f2a3c)"></div>
  <div class="card-label">System Integration &amp;<br>Optimization</div>
  <svg class="card-icon" width="56" height="56" viewBox="0 0 56 56" fill="none" stroke="#0677BA" stroke-width="2.4">
    <rect x="4" y="6" width="48" height="34" rx="3"/><path d="M20 40 L18 50 M36 40 L38 50 M14 50 H42"/>
    <circle cx="28" cy="23" r="7" stroke="#00AB8E"/><path d="M10 14 H18 M38 32 H46 M10 32 H16" stroke="#00AB8E"/>
  </svg>
</article>
<article class="abs card" style="left:789px;top:1556px">
  <div class="card-media" role="img" aria-label="Digital cloud glowing over a server landscape" style="background:radial-gradient(ellipse 35% 35% at 50% 38%,rgba(230,140,150,.7) 0%,transparent 100%),radial-gradient(ellipse 60% 20% at 50% 92%,rgba(240,90,60,.55) 0%,transparent 100%),linear-gradient(180deg,#4a7eab 0%,#2f5b8a 50%,#1a2846 100%)"></div>
  <div class="card-label">Cloud &amp; Infrastructure<br>Solutions</div>
  <svg class="card-icon" width="54" height="52" viewBox="0 0 54 52" fill="none" stroke="#0677BA" stroke-width="2.4">
    <path d="M14 32 H42 A10 10 0 0 0 40 12 A13 13 0 0 0 15 14 A9 9 0 0 0 14 32Z"/>
    <path d="M20 20 H36 M20 25 H36" stroke="#00AB8E"/>
    <path d="M27 32 V44 M17 32 V40 M37 32 V40"/><circle cx="27" cy="47" r="3"/><circle cx="17" cy="43" r="3"/><circle cx="37" cy="43" r="3"/>
  </svg>
</article>

<!-- products -->
<h2 class="abs sec-title" style="top:2076px">OUR <span class="accent">PRODUCTS</span></h2>
<div class="abs rule" style="left:549px;top:2146px;width:86px"></div>
<div class="abs product" role="img" aria-label="Server room with glowing network connection lines"></div>
<h3 class="abs product-title">&nbsp;Software<br>Architecture</h3>
<p class="abs product-text">Lorem Ipsum is simply dummy text of the printing and typesetting industry. Lorem Ipsum has been the industry's</p>
<a class="abs btn-ghost product-btn" href="#">READ MORE</a>

<!-- cta -->
<section class="abs cta" role="img" aria-label="Soft light network background"></section>
<h2 class="abs cta-title">LET’S BUILD THE FUTURE OF IT<br>TOGETHER – <span class="accent">CONNECT WITH US</span></h2>
<a class="abs btn-grad cta-btn" href="#">CONTACT US</a>

<!-- footer -->
<svg class="abs" style="left:0;top:2920px" width="1200" height="140" viewBox="0 0 1200 140">
  <defs><linearGradient id="waveC" x1="0" x2="1"><stop offset="0" stop-color="#0677BA"/><stop offset="1" stop-color="#00AB8E"/></linearGradient></defs>
  <path d="M0,140 Q520,-40 1200,100 L1200,140Z" fill="#262626"/>
  <path d="M0,140 Q520,-40 1200,100" fill="none" stroke="url(#waveC)" stroke-width="12"/>
</svg>
<footer>
  <div class="abs footer-body"></div>
  <div class="abs footer-brand"><div class="dot"></div><div class="name">QR.KA<br>Horizon</div></div>
  <div class="abs f-col" style="left:402px;top:3077px">
    <h4>MAIN LINKS</h4>
    <a href="#">Home</a><a href="#">About Us</a><a href="#">Product</a><a href="#">Solution</a><a href="#">Why choose Us</a>
  </div>
  <div class="abs f-col" style="left:610px;top:3077px">
    <h4>OTHER LINKS</h4>
    <a href="#" style="margin-top:3px">Contact Us</a><a href="#">Terms and Conditions</a><a href="#">Our Careers</a><a href="#">Privacy Policy</a>
  </div>
  <div class="abs f-col newsletter" style="left:857px;top:3077px">
    <h4>NEWSLETTER</h4>
    <p>We Will Notify You Of Any<br>Important News</p>
  </div>
  <div class="abs news-input"><span>Your Email Address</span>
    <svg width="26" height="24" viewBox="0 0 26 24" fill="none" stroke="#0677BA" stroke-width="1.8"><path d="M2 10 L24 2 L17 22 L12 13 Z M12 13 L24 2"/></svg>
  </div>
  <div class="abs footer-rule"></div>
  <p class="abs copyright">© 2025 QR.KA Horizon I All Rights Reserved</p>
</footer>

</body>
</html>
```